Upscale business cards needed for Board of Directors

We need professional business cards created for members of our family business Board of Directors. We would like these relatively simple and straightforward, but also with a unique element to set them apart. Probably stick with neutral and simple colors - white, grey etc. We need space for the traditional elements, including name, title, address, email/phone number. And we will be creating several from this template so it needs to be template that is easy to switch information in and out of.
Business
See description

```html
<!DOCTYPE html>
<html lang="en">
<head>
<meta charset="utf-8">
<title>Harborline Holdings – Business Cards</title>
<link href="https://fonts.googleapis.com/css2?family=Lato:wght@400;900&display=swap" rel="stylesheet">
<style>
  :root {
    --backdrop: #3a3a3a;
    --card-white: #ffffff;
    --ink: #111111;
    --band: #050505;
    --gold: #b9a878;
    --text-light: #f2f2f2;
    --muted: #333333;
  }
  * { margin: 0; padding: 0; box-sizing: border-box; }
  html, body {
    width: 1200px; height: 900px; overflow: hidden;
    background: var(--backdrop);
    font-family: "Lato", sans-serif;
  }
  .canvas {
    position: relative; width: 1200px; height: 900px;
  }
  .card {
    position: absolute; left: 285px; width: 630px; height: 360px;
    background: var(--card-white);
    box-shadow: 0 10px 30px rgba(0,0,0,0.45);
    overflow: hidden;
  }
  .card--front { top: 60px; }
  .card--back { top: 480px; }

  .wordmark {
    font-family: "Lato", sans-serif;
    font-weight: 900;
    color: var(--ink);
    text-transform: uppercase;
    line-height: 1;
    text-align: center;
  }
  .wordmark span { display: block; }

  .card--front .wordmark {
    position: absolute; left: 0; right: 0; top: 118px;
    font-size: 46px; letter-spacing: 2px;
  }
  .card--front .wordmark span + span { margin-top: 6px; letter-spacing: 14px; }
  .front-url {
    position: absolute; left: 0; right: 0; top: 282px;
    text-align: center; font-size: 15px; letter-spacing: 2px; color: var(--muted);
  }

  .back-top { position: absolute; left: 0; top: 0; width: 100%; height: 150px; }
  .card--back .wordmark {
    position: absolute; right: 50px; top: 34px;
    font-size: 38px; letter-spacing: 1px;
  }
  .card--back .wordmark span + span { margin-top: 6px; letter-spacing: 11px; }
  .gold-rule {
    position: absolute; left: 0; top: 150px; width: 100%; height: 3px; background: var(--gold);
  }
  .band {
    position: absolute; left: 0; top: 153px; width: 100%; height: 180px;
    background: var(--band); color: var(--text-light);
  }
  .person { position: absolute; left: 40px; top: 18px; }
  .person__name { font-size: 22px; font-weight: 400; }
  .person__title { font-size: 14px; color: var(--gold); margin-top: 2px; }
  .person__address { font-size: 16px; margin-top: 22px; line-height: 1.3; }

  .contacts {
    position: absolute; right: 60px; top: 58px; list-style: none;
  }
  .contacts li {
    display: flex; align-items: center; gap: 14px;
    font-size: 17px; line-height: 1.5;
  }
  .contacts svg { width: 14px; height: 14px; fill: var(--gold); flex: none; }
</style>
</head>
<body>
<main class="canvas">

  <section class="card card--front" aria-label="Card front">
    <div class="wordmark"><span>Harborline</span><span>Holdings</span></div>
    <p class="front-url">www.harborline.com</p>
  </section>

  <section class="card card--back" aria-label="Card back">
    <div class="back-top">
      <div class="wordmark"><span>Harborline</span><span>Holdings</span></div>
    </div>
    <div class="gold-rule"></div>
    <div class="band">
      <div class="person">
        <p class="person__name">Daniel Whitmore</p>
        <p class="person__title">Director</p>
        <p class="person__address">1450 Cedar Lane<br>Marlow TX 78100</p>
      </div>
      <ul class="contacts">
        <li>
          <svg viewBox="0 0 16 16" aria-hidden="true"><path d="M3 1h3l1.5 4-2 1.3a9 9 0 0 0 4.2 4.2L11 8.5l4 1.5v3a2 2 0 0 1-2 2A12 12 0 0 1 1 3a2 2 0 0 1 2-2z"/></svg>
          555 014 2200
        </li>
        <li>
          <svg viewBox="0 0 16 16" aria-hidden="true"><rect x="4" y="1" width="8" height="4"/><rect x="1" y="6" width="14" height="6" rx="1"/><rect x="4" y="10" width="8" height="5"/></svg>
          555 014 2201
        </li>
        <li>
          <svg viewBox="0 0 16 16" aria-hidden="true"><path d="M1 3h14v10H1z M1 3l7 6 7-6" stroke="#050505" stroke-width="1"/></svg>
          info@harborline.com
        </li>
        <li>
          <svg viewBox="0 0 16 16" aria-hidden="true"><circle cx="8" cy="8" r="7"/><path d="M1 8h14M8 1v14M3 4h10M3 12h10" stroke="#050505" stroke-width="1" fill="none"/></svg>
          www.harborline.com
        </li>
      </ul>
    </div>
  </section>

</main>
</body>
</html>
```